Landing page design for my current website

I need a landing page designed for my Wordpress website. My website is Velmorquay.com, and I need a page that will serve as a landing page for online ads I run. Please follow the color scheme of the current website

This web page will be targeted towards real estate owners who are looking for a property manager. Above the fold needs to have a CTA form headlined with "As a Rental Property Owner, I Want More Protection, Less Stress, and Drama-Free Living"

A few highlights that can be listed beyond the CTA and fold

- Comprehensive Property Management
Full-service management covering tenant placement, leasing, maintenance, and inspections.

Maximized Rental Income
Proven strategies to optimize rental rates and minimize vacancies, ensuring higher ROI.

Stress-Free Management
We handle all tenant interactions, maintenance requests, and property issues, so you don't have to.

Experienced Team
Over a decade of experience in managing single-family homes, small multifamily units, and apartment complexes.

Advanced Technology
Utilize cutting-edge property management software for efficient communication, rent collection, and maintenance tracking.

Tenant Screening and Placement
Thorough background checks and tenant screening processes to ensure reliable and responsible tenants.

Regular Property Inspections
Routine inspections to maintain property condition and address issues before they become costly problems.

Legal Compliance
Expertise in local and federal rental laws to keep your properties compliant and avoid legal hassles.

Transparent Reporting
Detailed monthly reports and financial statements to keep you informed about your property's performance.

Personalized Service
Tailored management plans to meet the unique needs of your properties and investment goals.
Effective Tenant Conflict Resolution
Skilled in handling challenging tenant situations, ensuring conflicts are resolved quickly and professionally to maintain a peaceful living environment and protect your investment.

```html
<!DOCTYPE html>
<html lang="en">
<head>
<meta charset="utf-8">
<title>Velmorquay Realty – Rental Property Owners</title>
<link href="https://fonts.googleapis.com/css2?family=Roboto:wght@400;500;700;900&display=swap" rel="stylesheet">
<style>
  :root{
    --brand-blue:#17427a;
    --deep-blue:#0d3a78;
    --ink:#333333;
    --muted:#6b6b6b;
    --white:#ffffff;
    --field-text:#555555;
  }
  *{margin:0;padding:0;box-sizing:border-box}
  html,body{width:861px;height:1200px;overflow:hidden;background:var(--white)}
  body{font-family:"Roboto",Arial,sans-serif;position:relative;color:var(--ink)}

  .top-rule{position:absolute;left:0;top:0;width:861px;height:3px;background:var(--brand-blue)}

  .site-header{position:absolute;left:0;top:3px;width:861px;height:101px}
  .brand{position:absolute;left:234px;top:27px;display:flex;align-items:center;gap:14px}
  .brand-dot{width:52px;height:52px;border-radius:50%;border:4px solid var(--brand-blue)}
  .brand-name{font-weight:700;font-size:27px;letter-spacing:1.5px;color:var(--brand-blue);text-transform:uppercase}
  .menu-button{position:absolute;left:703px;top:37px;width:76px;height:29px;border-radius:15px;background:var(--brand-blue);display:flex;align-items:center}
  .menu-button .menu-icon{width:23px;height:23px;margin-left:3px;border-radius:50%;background:var(--white);display:flex;align-items:center;justify-content:center}
  .menu-button .menu-label{margin-left:11px;color:var(--white);font-size:8.5px;font-weight:700;letter-spacing:.3px}

  .hero{position:absolute;left:0;top:104px;width:861px;height:399px;overflow:hidden}
  .hero-photo{position:absolute;inset:0;background:linear-gradient(100deg,#e9dccb 0%,#d9cbb8 30%,#b7b2aa 55%,#8e9a93 80%,#c9ccc6 100%)}
  .hero-photo::after{content:"";position:absolute;left:0;right:0;bottom:0;height:45%;background:linear-gradient(180deg,rgba(120,120,125,0) 0%,rgba(110,110,115,.45) 100%)}
  .hero-disc{position:absolute;left:393px;top:19px;width:382px;height:382px;border-radius:50%;background:rgba(13,58,120,.92)}
  .hero-ring{position:absolute;left:405px;top:31px;width:358px;height:358px;border-radius:50%;border:1.3px dashed rgba(255,255,255,.85)}
  .hero-title{position:absolute;left:393px;width:382px;top:83px;text-align:center;color:var(--white);font-weight:700;font-size:32px;line-height:43px;text-transform:uppercase}
  .hero-sub{position:absolute;left:393px;width:382px;top:178px;text-align:center;color:var(--white);font-weight:500;font-size:12px}
  .lead-form{position:absolute;left:434px;top:217px;width:301px}
  .lead-form .field{position:absolute;width:145px;height:32px;border-radius:16px;background:var(--white);border:none;font-family:inherit;font-size:9px;color:var(--field-text);padding-left:16px;display:flex;align-items:center}
  .lead-form .send{position:absolute;left:93px;top:88px;width:115px;height:33px;border-radius:17px;border:1.3px solid var(--white);color:var(--white);font-size:9.5px;display:flex;align-items:center;justify-content:center}

  .features{position:absolute;left:0;top:503px;width:861px;height:659px}
  .features-backdrop{position:absolute;inset:0;background:linear-gradient(180deg,#ffffff 0%,#ffffff 35%,#f2f2f3 70%,#e6e6e8 100%)}
  .feature-wheel{position:absolute;left:0;top:0}
  .feature{position:absolute;width:200px}
  .feature h3{font-size:9px;font-weight:700;color:var(--brand-blue);text-transform:uppercase;letter-spacing:.1px;margin-bottom:6px}
  .feature p{font-size:8.4px;line-height:16px;color:var(--muted)}
  .feature.right{text-align:right}
  .feature.center{text-align:center}
  .wheel-title-top{position:absolute;left:340px;top:283px;width:190px;text-align:center;font-size:26px;font-weight:700;color:var(--brand-blue)}
  .wheel-title-main{position:absolute;left:320px;top:346px;width:200px;text-align:center;font-size:29px;font-weight:900;color:var(--ink)}
  .view-more{position:absolute;left:377px;top:584px;width:107px;height:30px;border-radius:15px;background:var(--ink);color:var(--white);font-size:9px;font-weight:700;display:flex;align-items:center;justify-content:center}

  .site-footer{position:absolute;left:0;top:1162px;width:861px;height:38px;background:var(--brand-blue);color:var(--white);font-size:9px;font-weight:700;display:flex;align-items:center;justify-content:center}
</style>
</head>
<body>
  <div class="top-rule"></div>

  <header class="site-header">
    <div class="brand">
      <div class="brand-dot"></div>
      <div class="brand-name">Velmorquay Realty</div>
    </div>
    <div class="menu-button">
      <span class="menu-icon">
        <svg width="10" height="8" viewBox="0 0 10 8"><path d="M1 1.5h8M1 4h6M1 6.5h4" stroke="#17427a" stroke-width="1" stroke-linecap="round"/></svg>
      </span>
      <span class="menu-label">MENU</span>
    </div>
  </header>

  <section class="hero">
    <div class="hero-photo" role="img" aria-label="Photo of a family touring a bright, empty home interior with large windows"></div>
    <div class="hero-disc"></div>
    <div class="hero-ring"></div>
    <h1 class="hero-title">As a Rental<br>Property Owner</h1>
    <p class="hero-sub">I Want More Protection, Less Stress, &amp; Drama-Free Living</p>
    <form class="lead-form">
      <div class="field" style="left:0;top:0">Full Name</div>
      <div class="field" style="left:156px;top:0">Email Address</div>
      <div class="field" style="left:0;top:43px">Contact Number</div>
      <div class="field" style="left:156px;top:43px">Message</div>
      <div class="send">Send Message</div>
    </form>
  </section>

  <section class="features">
    <div class="features-backdrop" role="img" aria-label="Soft light-grey abstract block pattern background"></div>

    <svg class="feature-wheel" width="861" height="659" viewBox="0 503 861 659">
      <g fill="none" stroke="#17427a" stroke-width="5" stroke-linecap="round">
        <path d="M304 907 A150 150 0 1 0 278 856"/>
        <path d="M262 842 L278 860 L291 836"/>
      </g>
      <circle cx="303" cy="908" r="5" fill="#17427a"/>
      <g fill="#fff" stroke="#17427a" stroke-width="5">
        <circle cx="413" cy="666" r="37"/>
        <circle cx="540" cy="720" r="36"/>
        <circle cx="298" cy="747" r="39"/>
        <circle cx="574" cy="829" r="28"/>
        <circle cx="528" cy="931" r="28"/>
        <circle cx="435" cy="967" r="24"/>
        <circle cx="339" cy="947" r="22"/>
      </g>
      <!-- network -->
      <g stroke="#333" stroke-width="1.6" fill="none">
        <circle cx="413" cy="666" r="18"/>
        <path d="M413 648 L424 660 L413 684 L402 660 Z M395 666 H431 M402 660 L424 660 M413 648 V684"/>
      </g>
      <g fill="#333">
        <circle cx="413" cy="648" r="3"/><circle cx="413" cy="684" r="3"/><circle cx="395" cy="666" r="3"/><circle cx="431" cy="666" r="3"/>
        <circle cx="402" cy="660" r="2.5"/><circle cx="424" cy="660" r="2.5"/><circle cx="413" cy="666" r="2.5"/>
      </g>
      <!-- gear / tech -->
      <g>
        <circle cx="535" cy="720" r="12" fill="none" stroke="#333" stroke-width="5" stroke-dasharray="4 2.5"/>
        <path d="M540 707 V733" stroke="#fff" stroke-width="3"/>
        <g stroke="#333" stroke-width="1.4"><path d="M542 712 H552 M542 720 H556 M542 728 H552 M548 712 V706 M548 728 V734"/></g>
        <g fill="#333"><circle cx="552" cy="712" r="1.8"/><circle cx="556" cy="720" r="1.8"/><circle cx="552" cy="728" r="1.8"/></g>
      </g>
      <!-- document with shield -->
      <g>
        <rect x="280" y="728" width="28" height="36" rx="2" fill="#333"/>
        <g stroke="#fff" stroke-width="2"><path d="M285 736 H303 M285 742 H303 M285 748 H297 M285 754 H295"/></g>
        <path d="M307 748 L316 751 V758 C316 763 312 766 307 768 C302 766 298 763 298 758 V751 Z" fill="#333" stroke="#fff" stroke-width="1.5"/>
        <path d="M303 757 L306 760 L311 754" stroke="#fff" stroke-width="1.6" fill="none"/>
      </g>
      <!-- team -->
      <g fill="#333">
        <circle cx="574" cy="822" r="5"/><circle cx="564" cy="825" r="4"/><circle cx="584" cy="825" r="4"/>
        <path d="M565 840 C565 830 583 830 583 840 Z"/><path d="M556 838 C556 830 566 830 566 834 V838 Z"/><path d="M592 838 C592 830 582 830 582 834 V838 Z"/>
      </g>
      <!-- tools -->
      <g stroke="#333" stroke-width="2.6" stroke-linecap="round" fill="none">
        <path d="M517 920 L540 943"/><path d="M538 920 L519 939"/>
        <circle cx="517" cy="941" r="3.5"/><circle cx="539" cy="921" r="3.5"/>
      </g>
      <!-- money bag -->
      <g>
        <path d="M430 955 H440 L437 960 C446 964 448 976 435 978 C422 976 424 964 433 960 Z" fill="#333"/>
        <text x="435" y="975" text-anchor="middle" font-size="9" font-weight="700" fill="#fff" font-family="Roboto, sans-serif">$</text>
      </g>
      <!-- building -->
      <g fill="#333">
        <rect x="330" y="938" width="10" height="20"/><rect x="341" y="944" width="8" height="14"/>
        <g fill="#fff"><rect x="332" y="941" width="2" height="2"/><rect x="336" y="941" width="2" height="2"/><rect x="332" y="946" width="2" height="2"/><rect x="336" y="946" width="2" height="2"/><rect x="332" y="951" width="2" height="2"/><rect x="336" y="951" width="2" height="2"/><rect x="343" y="947" width="2" height="2"/><rect x="343" y="952" width="2" height="2"/></g>
      </g>
    </svg>

    <div class="wheel-title-top">OUR</div>
    <div class="wheel-title-main">FEATURES</div>

    <div class="feature center" style="left:293px;top:59px;width:240px">
      <h3>Tenant Screening and Placement</h3>
      <p>Thorough background checks and tenant screening<br>processes to ensure reliable &amp; responsible tenants.</p>
    </div>
    <div class="feature" style="left:600px;top:181px;width:220px">
      <h3>Advanced Technology</h3>
      <p>Utilize cutting-edge property management<br>software for efficient communication</p>
    </div>
    <div class="feature right" style="left:28px;top:222px">
      <h3>Legal Compliance</h3>
      <p>Expertise in local and federal rental laws<br>to keep your properties compliant and<br>avoid legal hassles.</p>
    </div>
    <div class="feature" style="left:619px;top:310px;width:220px">
      <h3>Experienced Team</h3>
      <p>Over a decade of experience in managing<br>single-family homes</p>
    </div>
    <div class="feature" style="left:574px;top:412px;width:220px">
      <h3>Stress-Free Management</h3>
      <p>We handle all tenant interactions,<br>maintenance requests, and property issues,</p>
    </div>
    <div class="feature right" style="left:60px;top:437px;width:240px">
      <h3>Comprehensive Property Management</h3>
      <p>Full-service management covering tenant<br>placement, leasing, maintenance, and inspections.</p>
    </div>
    <div class="feature" style="left:414px;top:503px;width:220px">
      <h3>Maximized Rental Income</h3>
      <p>Proven strategies to optimize rental rates and<br>minimize vacancies, ensuring higher ROI.</p>
    </div>

    <div class="view-more">VIEW MORE</div>
  </section>

  <footer class="site-footer">(C) COPYRIGHT 2024 | ALL RIGHTS RESERVED</footer>
</body>
</html>
```